Animal Eye Clinic needs a Business card

We are a new veterinary ophthalmology practice (Ridgeline Pet Vision Care) and we need a business card designed. We only see animal eyes - we are not a regular veterinary clinic. We already have a logo. We are looking for a professional, good looking business card to hand out to our clients. We are looking for something simple but professional and contemporary. Our logo is likely the only picture/graphic that needs to be on the card.
Updates

Contact Information for Business Card

Delia Vossman, BSc, DVM, MSc, DipACVO
Veterinary Ophthalmologist

Phone: 250.418.3927
Email: ridgelinepetvisioncare@mailbox-example.net
Website: ridgelinepetvisioncare-example.net
Address: 1874 Thornbury Rd
Kelowna, BC, V1X 4M9

Colors

Designer to choose colors to be used in the design.

Requirements
Must have
• Our logo (attached)

```html
<!DOCTYPE html>
<html lang="en">
<head>
<meta charset="utf-8">
<title>Ridgeline Pet Vision Care – Business Card</title>
<link href="https://fonts.googleapis.com/css2?family=Roboto:wght@400;500;700&display=swap" rel="stylesheet">
<style>
  :root {
    --bg: #e9e8e6;
    --card: #2a2a2c;
    --card-edge: #1b8e9b;
    --teal: #1a93a1;
    --ink: #f2f2f2;
    --muted-teal: #1f8c98;
    --deco-light: #38383b;
    --deco-dark: #1f1f21;
  }
  * { box-sizing: border-box; margin: 0; padding: 0; }
  html, body { width: 1200px; height: 847px; overflow: hidden; }
  body {
    background: var(--bg);
    font-family: "Roboto", Arial, sans-serif;
    display: flex;
    align-items: center;
    justify-content: center;
    gap: 50px;
  }
  .card {
    position: relative;
    width: 540px;
    height: 309px;
    background: var(--card);
    border-bottom: 4px solid var(--card-edge);
    border-right: 2px solid var(--card-edge);
    box-shadow: 0 10px 24px rgba(0,0,0,.25);
    overflow: hidden;
  }
  .brand {
    display: flex;
    align-items: center;
    gap: 12px;
    color: var(--teal);
    font-weight: 700;
    text-transform: uppercase;
    line-height: 1.1;
  }
  .brand-dot {
    flex: none;
    border-radius: 50%;
    background: var(--teal);
  }
  .card-front .brand {
    position: absolute;
    left: 50%; top: 50%;
    transform: translate(-50%, -50%);
    font-size: 28px;
  }
  .card-front .brand-dot { width: 40px; height: 40px; }

  .card-back .brand {
    position: absolute;
    left: 210px; top: 30px;
    font-size: 17px;
    gap: 9px;
  }
  .card-back .brand-dot { width: 26px; height: 26px; }

  .decoration {
    position: absolute;
    right: 0; bottom: 0;
    width: 215px; height: 215px;
    border-top-left-radius: 110px;
    background: radial-gradient(circle at 60% 40%, var(--deco-light), var(--deco-dark));
  }
  .person {
    position: absolute;
    left: 34px; top: 78px;
    color: var(--ink);
  }
  .person-name {
    display: flex;
    align-items: center;
    gap: 8px;
    color: var(--teal);
    font-size: 20px;
    font-weight: 700;
    text-transform: uppercase;
    margin-left: -16px;
  }
  .person-name svg { width: 10px; height: 12px; fill: var(--teal); }
  .credentials { color: var(--muted-teal); font-size: 12.5px; margin-top: 2px; }
  .role { font-size: 14px; margin-top: 2px; }
  .address { font-size: 14px; line-height: 1.35; margin-top: 14px; }
  .contact { list-style: none; margin-top: 10px; font-size: 13.5px; line-height: 1.45; }
  .contact li { display: flex; align-items: center; gap: 6px; }
  .contact svg { width: 11px; height: 11px; fill: var(--teal); flex: none; }
</style>
</head>
<body>

<section class="card card-front" aria-label="Card front">
  <div class="brand"><span class="brand-dot"></span><span>Ridgeline Pet<br>Vision Care</span></div>
</section>

<section class="card card-back" aria-label="Card back">
  <div class="decoration" role="img" aria-label="Embossed tone-on-tone animal silhouettes"></div>
  <div class="brand"><span class="brand-dot"></span><span>Ridgeline Pet<br>Vision Care</span></div>

  <div class="person">
    <h1 class="person-name"><svg viewBox="0 0 10 12"><path d="M0 0 10 6 0 12z"/></svg>Delia Vossman</h1>
    <p class="credentials">BSc, DVM, MSc, DipACVO</p>
    <p class="role">Veterinary Ophthalmologist</p>
    <p class="address">1874 Thornbury Rd<br>Kelowna, BC, V1X 4M9</p>
    <ul class="contact">
      <li><svg viewBox="0 0 24 24"><path d="M6.6 10.8a15 15 0 0 0 6.6 6.6l2.2-2.2c.3-.3.7-.4 1-.2 1.1.4 2.3.6 3.6.6.6 0 1 .4 1 1V20c0 .6-.4 1-1 1A17 17 0 0 1 3 4c0-.6.4-1 1-1h3.5c.6 0 1 .4 1 1 0 1.3.2 2.5.6 3.6.1.3 0 .7-.2 1z"/></svg>250.418.3927</li>
      <li><svg viewBox="0 0 24 24"><path d="M2 5h20v14H2zm2 2v.5l8 5 8-5V7l-8 5z"/></svg>ridgelinepetvisioncare@mailbox-example.net</li>
      <li><svg viewBox="0 0 24 24"><circle cx="12" cy="12" r="10"/></svg>ridgelinepetvisioncare-example.net</li>
    </ul>
  </div>
</section>

</body>
</html>
```